Update our OBGYN business card look and info

We are an OBGYN office. Our logo is nice but would like to "woman" part of the logo to be a darker color, to contrast with the flower that surrounds it. Maybe make our practice name Bloom Harbor Health more feminine. Our practice caters to women only. All providers and staff are female.

Target Market(s)

Females 16-65.

Industry/Entity Type

Business

Contact Information for Business Card

See attached upload. The ONLY CHANGE to the information is DELETE the name Paula Renwick, Midwife and REPLACE with Dora Fintelli, Midwife

Logo Text

Bloom Harbor Health Obstetrics & Gynecology

Font styles to use
Serif
Script

Colors
85cae6
0692cd
33a6d7
85abd2
f59195
eea4c8
cadf82
fac994
d3a5cc

```html
<!DOCTYPE html>
<html lang="en">
<head>
<meta charset="utf-8">
<title>Bloom Harbor Health – Business Card</title>
<link rel="stylesheet" href="https://fonts.googleapis.com/css2?family=Cinzel:wght@400;500&family=Open+Sans:wght@400;600&display=swap">
<style>
  :root {
    --stage: #111111;
    --white: #ffffff;
    --brand-blue: #0692cd;
    --band-blue: #0a8fcd;
    --pattern-blue: #1596d3;
    --pattern-light: #33a6d7;
    --brand-green: #8cc21a;
    --text-white: #ffffff;
  }
  * { margin: 0; padding: 0; box-sizing: border-box; }
  html, body {
    width: 1200px; height: 900px; overflow: hidden;
    background: var(--stage);
  }
  .stage { position: relative; width: 1200px; height: 900px; }

  .card {
    position: absolute; top: 306px; height: 271px;
    border-radius: 10px; overflow: hidden;
  }
  .card-front { left: 149px; width: 439px; background: var(--white); }
  .card-back  { left: 608px; width: 441px; }

  /* Front – brand header */
  .brand {
    position: absolute; left: 0; top: 0; width: 100%; height: 100px;
    display: flex; align-items: center; justify-content: center; gap: 12px;
  }
  .brand-dot {
    width: 46px; height: 46px; border-radius: 50%;
    background: var(--brand-blue);
  }
  .brand-name {
    font-family: "Open Sans", sans-serif; font-weight: 600;
    color: var(--brand-blue); font-size: 13px; line-height: 18px;
  }
  .brand-name span { display: block; }
  .brand-name .brand-title { text-transform: uppercase; letter-spacing: 0.2px; }

  /* Front – providers band */
  .providers {
    position: absolute; left: 0; top: 100px; width: 100%; height: 91px;
    background: var(--band-blue);
    font-family: "Cinzel", serif; color: var(--text-white);
    font-size: 14px; letter-spacing: 0.3px;
  }
  .provider { position: absolute; white-space: nowrap; line-height: 1; }
  .provider.col-left { left: 19px; }
  .provider.col-right { right: 23px; text-align: right; }

  /* Front – contact band */
  .contact {
    position: absolute; left: 0; top: 191px; width: 100%; height: 80px;
    background: var(--brand-green);
    font-family: "Open Sans", sans-serif; color: var(--text-white);
    font-size: 12px;
  }
  .contact-list { position: absolute; left: 23px; top: 15px; list-style: none; }
  .contact-list li {
    display: flex; align-items: center; gap: 3px; height: 16px; line-height: 16px;
  }
  .contact-list svg { width: 10px; height: 10px; fill: var(--text-white); }
  .address {
    position: absolute; right: 23px; top: 31px; text-align: right;
    font-style: normal; line-height: 16px;
  }

  /* Back */
  .back-pattern {
    width: 100%; height: 100%;
    background: radial-gradient(circle at 70% 65%, var(--pattern-light) 0%, var(--pattern-blue) 60%);
  }
</style>
</head>
<body>
<main class="stage">

  <section class="card card-front" aria-label="Business card front">
    <header class="brand">
      <div class="brand-dot" aria-hidden="true"></div>
      <div class="brand-name">
        <span class="brand-title">Bloom Harbor Health</span>
        <span class="brand-sub">Obstetrics &amp; Gynecology</span>
      </div>
    </header>

    <div class="providers">
      <p class="provider col-left" style="top:15px">Marian Coley,MD</p>
      <p class="provider col-left" style="top:39px">Lena Hartwell,MD</p>
      <p class="provider col-left" style="top:63px">Lena Hartwell,MD</p>
      <p class="provider col-right" style="top:39px">Dora Fintelli, Midwife</p>
      <p class="provider col-right" style="top:63px">Ruth Ambrose,Midwife</p>
    </div>

    <div class="contact">
      <ul class="contact-list">
        <li>
          <svg viewBox="0 0 10 10" aria-hidden="true"><path d="M2 0.5 L3.6 2.6 L2.8 3.6 Q4 6 6.4 7.2 L7.4 6.4 L9.5 8 L8.4 9.5 Q3.5 9 0.5 1.6 Z"/></svg>
          555-014-2738
        </li>
        <li>
          <svg viewBox="0 0 10 10" aria-hidden="true"><path d="M2 0.5h5v3h2v6H1v-6h1zM3 1.5v2h3v-2zM2.5 5v1h1V5zm2 0v1h1V5zm2 0v1h1V5zM2.5 7v1h1V7zm2 0v1h1V7zm2 0v1h1V7z"/></svg>
          555-014-6153
        </li>
        <li>
          <svg viewBox="0 0 10 10" aria-hidden="true"><circle cx="5" cy="5" r="4.5"/></svg>
          www.bloomharborhealth.com
        </li>
      </ul>
      <address class="address">
        240 Alder Lane Ste 3B<br>
        Fairview,GA 30000-0142
      </address>
    </div>
  </section>

  <section class="card card-back" aria-label="Business card back">
    <div class="back-pattern" role="img" aria-label="Blue background with a faint repeating flower motif and a small emblem"></div>
  </section>

</main>
</body>
</html>
```